TRELOS - Web Design Project

Task Description
RELOS is the major GLOVRA project supporting the Indonesian Bureau of Tidal Works and Harvests (BTWH). BTWH is responsible for promoting sustainable use of fish and other marine resources for Indonesia’s long-term economic prosperity. Its mandate encompasses such issues as drafting of marine and fisheries sector policies; control of overfishing, destructive and illegal fishing practices; spatial planning for resource use; management of conservation areas; data analysis and modeling for fisheries management; and promoting the long-term welfare of fishing communities. The TRELOS project is supporting BTWH efforts to achieve sustainability in the marine and fisheries sector and to improve the response of coastal communities to near-term disasters and long-term impacts related to climate change.

The TRELOS project has three key thematic areas: [policy] [1], [sustainable fisheries] [2], and [climate change] [3] — as well as supporting overall coordination of [Coastal Stewardship Scheme] [4] activities.
Updates

Project Deadline Extended
Reason: There are two public holidays in Indonesia so we are unable to provide feedback to designers between 17th and the 20th.

a few people have asked for reference sites - there is really no reference site we can give but I have attached a jpg for some ideas - we are after innovated ideas that will capture people's attention but which is extermely easy to use and navigate. 

the main focus should be on a map on Indonesia with focal points of our three offices (and with great navigation buttons/tools). 

please give us something amazing and use your design skills to make an amazing site

thanks

Target Market(s)

under 25, college or uni - research students - others interested in marine and fisheries

Industry/Entity Type

Sustainability

Requirements
Must have
• The web must have Indonesia map on the center with button on Jakarta city as headquarter, Sulawesi Tenggara (Wakatobi) as branch office and Nusa Tenggara Barat (Mataram), must have an icon for navigation on the upper, left or bottom side. Example of layout is attached (only as example). The "buttons" should then be used as navigation tools

We are after innovative ideas that with easy navigation features.

Current website is www.trelosworks.com - this is seen as too hard to navigate

Navigation Icons will also need to be developed;
- About
- Activities
- News
Library
Press releases
Publications
- Partners
- Links

site will also need to adhere to these the GLOVRA branding guidelines
http://www.glovra.example/identity/GLOVRA_Visual_Rules_Guide.pdf

TRELOS Logo is attached

Nice to have
• - based on scaffold plinko, site will be hosted on stavelo9 platform. (http://plinko.codebarn.example/)

```html
<!DOCTYPE html>
<html lang="en">
<head>
<meta charset="utf-8">
<title>TRELOS – Indonesia Coastal and Tide Support</title>
<link href="https://fonts.googleapis.com/css2?family=Arimo:wght@400;700&display=swap" rel="stylesheet">
<style>
:root{
  --navy:#1b2f5c;
  --blue:#0a5fc4;
  --link:#1f5fa8;
  --red:#c4121a;
  --accent-red:#d11f36;
  --text:#666;
  --panel:#d9dadf;
  --bg:#ececec;
  --footer-top:#0b55b4;
  --footer-bottom:#062a6e;
}
*{box-sizing:border-box;margin:0;padding:0}
html,body{width:972px;height:1200px;overflow:hidden}
body{position:relative;background:var(--bg);font-family:"Arimo",Arial,sans-serif;color:var(--text);font-size:12px}
a{color:inherit;text-decoration:none}
.abs{position:absolute}

/* header */
.site-header{position:absolute;left:0;top:0;width:972px;height:92px;background:#fff;border-top:4px solid var(--accent-red)}
.brand{position:absolute;left:24px;top:14px;width:281px}
.brand-name{display:flex;align-items:center;gap:8px;font-weight:700;font-size:24px;color:var(--navy);letter-spacing:-.3px;height:36px}
.brand-mark{width:34px;height:34px;border-radius:50%;background:var(--navy)}
.brand-bar{margin-top:10px;height:16px;background:var(--navy);color:#fff;font-size:7.5px;font-weight:700;text-align:center;line-height:16px;border-bottom:3px solid var(--accent-red)}
.phone{position:absolute;left:614px;top:58px;display:flex;align-items:center;gap:8px;color:#888;font-size:14px}
.search{position:absolute;left:777px;top:56px;width:176px;height:26px;border:1px solid #d5d5d5;border-radius:2px;background:#fff}
.search span{position:absolute;left:11px;top:6px;color:#bbb;font-size:11.5px}
.search button{position:absolute;right:-1px;top:-1px;width:29px;height:26px;background:var(--blue);border:0;border-radius:0 2px 2px 0}

/* nav */
.main-nav{position:absolute;left:0;top:92px;width:972px;height:36px;background:linear-gradient(#fafafa,#e4e4e4);border-top:1px solid #ddd;border-bottom:1px solid #d0d0d0}
.nav-item{position:absolute;top:5px;display:flex;align-items:center;gap:8px;font-weight:700;font-size:12px;color:var(--link);white-space:nowrap}
.nav-icon{width:24px;height:24px;border-radius:4px}

/* hero */
.hero{position:absolute;left:0;top:128px;width:972px;height:378px}
.map{position:absolute;left:14px;top:8px;width:722px;height:364px;background:radial-gradient(ellipse at 50% 50%,#3c86de 0%,#a9c8ef 55%,#e9e9e9 80%);border-radius:40px}
.pin{position:absolute;display:flex;flex-direction:column;align-items:center}
.pin-label{background:var(--navy);color:#fff;font-weight:700;font-size:10.5px;padding:4px 7px;border-radius:2px;position:relative}
.pin-label::after{content:"";position:absolute;left:50%;bottom:-5px;margin-left:-5px;border:5px solid transparent;border-bottom:0;border-top-color:var(--navy)}
.pin-dot{margin-top:7px;width:12px;height:12px;border-radius:50%;background:#fff;border:1px solid #cfd8e8}
.hero-panel{position:absolute;left:736px;top:11px;width:218px;height:357px;background:var(--panel);padding:25px 20px 0 22px}
.hero-panel h2{font-size:15.5px;color:var(--navy);font-weight:700;margin-bottom:19px;white-space:nowrap;letter-spacing:.1px}
.hero-panel p{font-size:11.5px;line-height:19px;color:#777;text-align:justify;margin-bottom:26px}
.more{font-weight:700;color:#555}

/* main */
.main{position:absolute;left:19px;top:511px;width:935px;height:595px;background:#fff;border:1px solid #ddd;box-shadow:0 0 4px rgba(0,0,0,.08)}
.feature{position:absolute;top:16px;width:212px;height:161px;border:1px solid #e3e3e3;background:linear-gradient(#fff 0,#fff 20%,#f4f4f4 100%)}
.feature-head{height:40px;background:linear-gradient(#fff,#ececec);border-bottom:1px solid #e3e3e3;display:flex;align-items:center;padding-left:8px;gap:10px}
.feature-icon{width:34px;height:34px;border-radius:50%;flex:none}
.feature-head h3{font-size:13px;font-weight:700;color:var(--link);line-height:15px}
.feature p{padding:12px 10px 0 10px;font-size:11.5px;line-height:19px;text-align:justify}
.feature .more{color:var(--red)}
.red{color:var(--red)}
.section-title{font-size:14px;color:#888;font-weight:400}
.section-title b{color:var(--link);font-weight:400}
.news{position:absolute;left:19px;top:203px;width:668px}
.news-title{font-size:13px;font-weight:700;color:var(--link)}
.news p{font-size:11.5px;line-height:19px;text-align:justify}
.news-rule{border-top:1px solid #e6e6e6}
.thumb{width:87px;height:65px;border:1px solid #ddd;background:radial-gradient(circle,#6d6fb2,#c7cbe4 70%,#fff 72%);flex:none}
.sidebar-box{position:absolute;left:704px;width:212px;border:1px solid #e3e3e3;background:#fff}
.sidebar-box h4{height:25px;background:linear-gradient(#fff,#ececec);border-bottom:1px solid #e3e3e3;font-size:14px;font-weight:700;color:var(--navy);padding:5px 0 0 12px}
.sidebar-box h4 span{color:var(--accent-red)}
.event{margin:0 12px;padding:8px 0 9px;border-bottom:1px dashed #d8d8d8;font-size:11.5px;line-height:17px;color:var(--link)}
.event b{display:block}
.gallery{position:absolute;top:455px;height:126px;border:2px solid #dfe6f0;background:#f7f9fc}
.shot{position:absolute;top:8px;height:106px;background:linear-gradient(#8cb3dc 0%,#d9e7f3 55%,#6b95b9 70%,#e8e4d4 100%)}
.arrow{position:absolute;width:24px;height:24px;border-radius:50%;background:#fff;border:2px solid #d5dff0}
.footer{position:absolute;left:0;top:1112px;width:972px;height:88px;background:linear-gradient(var(--footer-top),var(--footer-bottom));color:#d8e4f5;font-size:10.5px}
.footer-links{position:absolute;right:18px;top:12px;font-size:12px;color:#fff}
.social{position:absolute;top:40px;width:22px;height:22px;border-radius:3px}
</style>
</head>
<body>

<header class="site-header">
  <div class="brand">
    <div class="brand-name"><span class="brand-mark"></span>GLOVRA INDONESIA</div>
    <div class="brand-bar">INDONESIA COASTAL AND TIDE SUPPORT (TRELOS) PROJECT</div>
  </div>
  <div class="phone">
    <svg width="26" height="26" viewBox="0 0 26 26"><path d="M6 3l4 1 1 5-3 2c1 3 4 6 7 7l2-3 5 1 1 4c-1 2-3 3-5 3C10 22 4 16 3 8c0-2 1-4 3-5z" fill="#222"/><circle cx="20" cy="6" r="5" fill="#f2a51c"/></svg>
    +120 555 0142
  </div>
  <div class="search"><span>Search something...</span>
    <button aria-label="Search"><svg width="14" height="14" viewBox="0 0 14 14"><circle cx="6" cy="6" r="4" stroke="#fff" stroke-width="2" fill="none"/><path d="M9 9l4 4" stroke="#fff" stroke-width="2"/></svg></button>
  </div>
</header>

<nav class="main-nav">
  <a class="nav-item" style="left:21px"><span class="nav-icon" style="background:#1d7fe0;border-radius:50% 50% 6px 6px"></span>ABOUT US</a>
  <a class="nav-item" style="left:134px"><span class="nav-icon" style="background:#1565c8;border-radius:50%"></span>ACTIVITIES</a>
  <a class="nav-item" style="left:251px"><span class="nav-icon" style="background:#a4834a"></span>NEWS</a>
  <a class="nav-item" style="left:341px"><span class="nav-icon" style="background:linear-gradient(90deg,#e33 0 25%,#36c 25% 50%,#fc3 50% 75%,#3a3 75%)"></span>LIBRARY</a>
  <a class="nav-item" style="left:438px"><span class="nav-icon" style="background:#f1f1f1;border:2px solid #d33"></span>PRESS RELEASE</a>
  <a class="nav-item" style="left:569px"><span class="nav-icon" style="background:#2b8fd8"></span>PUBLICITY</a>
  <a class="nav-item" style="left:683px"><span class="nav-icon" style="background:linear-gradient(90deg,#e2343f 50%,#2d6fd0 50%);border-radius:50%"></span>PARTNERS</a>
  <a class="nav-item" style="left:803px"><span class="nav-icon" style="background:#9aa7c8;border-radius:50% 50% 2px 2px"></span>LINKS</a>
</nav>

<section class="hero">
  <div class="map" role="img" aria-label="Map of the Indonesian archipelago in blue"></div>
  <a class="pin" style="left:197px;top:258px;top:258px;transform:translateY(-128px)"><span class="pin-label">JAKARTA</span><span class="pin-dot"></span></a>
  <a class="pin" style="left:380px;top:77px"><span class="pin-label">SULAWESI</span><span class="pin-dot"></span></a>
  <a class="pin" style="left:359px;top:154px"><span class="pin-label">LOMBOK</span><span class="pin-dot"></span></a>
  <aside class="hero-panel">
    <h2>CONTENT TITLE HERE</h2>
    <p>Lorem ipsum dolor sit ipsumLorem ipsum dolor sit ipsumLorem ipsum dolor sit ipsumLorem ipsum dolor sit ipsumLorem ipsum dolor sit usm L orem ipsum dolor. <span class="more">More...</span></p>
    <p>Lorem ipsum dolor sit ipsumLorem ipsum dolor sit ipsumLorem ipsum dolor sit ipsumLorem ipsum dolor sit ipsumLorem ipsum dolor sit usm L orem ipsum dolor. <span class="more">More...</span></p>
  </aside>
</section>

<main class="main">
  <article class="feature" style="left:17px">
    <div class="feature-head"><span class="feature-icon" style="background:#1f6fc4;border-radius:6px"></span><h3>Policy</h3></div>
    <p>Lorem ipsum dolor sit ipsumLorem ipsum dolor sit ipsumLorem ipsum dolor sit ipsumLorem ipsum dolor sit ipsumLorem ipsum dolor sit usm L orem ipsum dolor. <span class="more">More...</span></p>
  </article>
  <article class="feature" style="left:246px">
    <div class="feature-head"><span class="feature-icon" style="background:#8fcf3a"></span><h3>Sustainable Fisheries</h3></div>
    <p>Lorem ipsum dolor sit ipsumLorem ipsum dolor sit ipsumLorem ipsum dolor sit ipsumLorem ipsum dolor sit ipsumLorem ipsum dolor sit usm L orem ipsum dolor. <span class="more">More...</span></p>
  </article>
  <article class="feature" style="left:475px">
    <div class="feature-head"><span class="feature-icon" style="background:linear-gradient(135deg,#1e63c0 45%,#7dc242 55%)"></span><h3>Climate Changes</h3></div>
    <p>Lorem ipsum dolor sit ipsumLorem ipsum dolor sit ipsumLorem ipsum dolor sit ipsumLorem ipsum dolor sit ipsumLorem ipsum dolor sit usm L orem ipsum dolor. <span class="more">More...</span></p>
  </article>
  <article class="feature" style="left:705px">
    <div class="feature-head"><svg class="feature-icon" viewBox="0 0 34 34"><path d="M18 3v24H6z" fill="#1a62c4"/><path d="M20 8l8 19h-8z" fill="#3a8ae0"/><path d="M4 29h26l-3 3H7z" fill="#1a62c4"/></svg><h3>Coastal Stewardship<br>Scheme</h3></div>
    <p>Lorem ipsum dolor sit ipsumLorem ipsum dolor sit ipsumLorem ipsum dolor sit ipsumLorem ipsum dolor sit ipsumLorem ipsum dolor sit usm L orem ipsum dolor. <span class="more">More...</span></p>
  </article>

  <section class="news">
    <h2 class="section-title" style="padding-bottom:9px;border-bottom:1px solid #e8e8e8">Letest <b>News</b></h2>
    <div style="padding:17px 0 12px">
      <div class="news-title">News Title Here</div>
      <p>Lorem ipsum dolor sit ipsumLorem ipsum dolor sit ipsumLorem ipsum dolor sit ipsumLorem ipsum dolor sit ipsumLoremLorem ipsum dolor sit ipsumLorem <span class="red">More...</span></p>
    </div>
    <div class="news-rule"></div>
    <div style="padding:9px 0 0">
      <div class="news-title" style="margin-bottom:6px">News Title Here</div>
      <div style="display:flex;gap:8px;align-items:flex-start">
        <div class="thumb" role="img" aria-label="Globe illustration"></div>
        <p style="flex:1;margin-top:-2px">Lorem ipsum dolor sit ipsumLorem ipsum dolor sit ipsumLorem ipsum dolor sit ipsumLorem ipsum dolor sit ipsumLoremLorem ipsum dolor sit ipsumLorem Lorem ipsum dolor sit ipsumLorem ipsum dolor sit ipsumLorem ipsum dolor sit ipsumLorem ipsum dol or sit jdlkgjdlgjdlk ipsumLorem ipsum dolor sit ipsumLorem <span class="red">More...</span></p>
      </div>
    </div>
  </section>

  <h2 class="section-title abs" style="left:19px;top:432px">Letest <b>Photos</b></h2>
  <h2 class="section-title abs" style="left:372px;top:434px">Letest <b>videos</b></h2>
  <div class="gallery" style="left:17px;width:336px">
    <div class="shot" role="img" aria-label="Beach photo, Pantai Biak" style="left:16px;width:147px"><span style="position:absolute;left:0;right:0;bottom:7px;text-align:center;color:#1b2f5c;font-weight:700;font-size:13px">Pantai Biak</span></div>
    <div class="shot" role="img" aria-label="Sky and sea photo" style="left:180px;width:147px"></div>
  </div>
  <span class="arrow" style="left:4px;top:514px"><svg width="20" height="20" viewBox="0 0 20 20"><path d="M13 5L6 10l7 5z" fill="#1b4fa0"/></svg></span>
  <span class="arrow" style="left:355px;top:514px"><svg width="20" height="20" viewBox="0 0 20 20"><path d="M7 5l7 5-7 5z" fill="#d11f36"/></svg></span>
  <div class="gallery" style="left:372px;width:315px">
    <div class="shot" role="img" aria-label="Video thumbnail of the sea" style="left:7px;width:141px"><svg class="abs" style="left:56px;top:40px" width="26" height="28"><path d="M26 0v28L0 14z" fill="#fff" opacity=".8"/></svg></div>
    <div class="shot" role="img" aria-label="Video thumbnail of the sea" style="left:163px;width:141px"><svg class="abs" style="left:56px;top:40px" width="26" height="28"><path d="M26 0v28L0 14z" fill="#fff" opacity=".8"/></svg></div>
  </div>

  <aside class="sidebar-box" style="top:199px;height:119px">
    <h4>Signup <span>Newsletter</span></h4>
    <div class="abs" role="img" aria-label="Globe and newspaper illustration" style="left:2px;top:28px;width:70px;height:58px;border-radius:50%;background:radial-gradient(circle,#4aa3ea,#cde4f6 70%,#fff 72%)"></div>
    <p class="abs" style="left:88px;top:36px;width:116px;font-size:11px;line-height:14px;color:#999;text-align:justify">ipsumLorem ipsum dolor sit ipsumLorem ipsum dolor sit</p>
    <div class="abs" style="left:4px;top:91px;width:142px;height:24px;border:1px solid #ddd;color:#ccc;font-size:11px;padding:5px 9px">Email here</div>
    <div class="abs" style="left:147px;top:91px;width:60px;height:24px;background:var(--blue);color:#fff;font-weight:700;font-size:11.5px;text-align:center;line-height:24px">SIGN UP</div>
  </aside>

  <aside class="sidebar-box" style="top:329px;height:252px">
    <h4>Meeting <span>Calendar</span></h4>
    <div class="event"><b>Date : 21-05-2012</b>Lorem ipsum dolor ispLorem ipsum dolor ispLorem ipsum dolor isp</div>
    <div class="event"><b>Date : 21-05-2012</b>Lorem ipsum dolor ispLorem ipsum dolor ispLorem ipsum dolor isp</div>
    <div class="event" style="border:0"><b>Date : 21-05-2012</b>Lorem ipsum dolor ispLorem ipsum dolor ispLorem ipsum dolor isp</div>
    <div style="text-align:right;padding-right:10px;color:var(--link);font-weight:700;font-size:11.5px">More....</div>
  </aside>
</main>

<footer class="footer">
  <div class="abs" style="left:20px;top:16px;line-height:18px">Copyright © 2012-2014 Halvercrest Associates Inc. TRELOS - Privacy policy<br>The information provided on this website is not official Aldmere Commonwealth information and does not represent the views<br>or positions of the Global Relief and Outreach Agency or the Aldmere Commonwealth.</div>
  <div class="footer-links">Home &nbsp; | &nbsp;About Us &nbsp; | &nbsp;Our Activities &nbsp; | &nbsp;Contact Us</div>
  <span class="social" style="left:875px;background:#5ab6cf"></span>
  <span class="social" style="left:903px;background:#3b5f9f"></span>
  <span class="social" style="left:931px;background:#f08a22"></span>
</footer>

</body>
</html>
```